Realtor branding business card

modern, simple and self branding. Broker office logo needs to be used but not emphasized. Looking to brand myself

Target Market(s)

buyers, sellers and investors

Industry/Entity Type

Realtor

Contact Information for Business Card

Sample of my current business card on file

Requirements
Must have
• my website - tobiasmerrowkl.com
• Realtor logo
• Fair housing logo
Nice to have
• Colors from office logo but not a must
Should not have
• Do not want headshot

```html
<!DOCTYPE html>
<html lang="en">
<head>
<meta charset="utf-8">
<title>Tobias Merrow – Realtor Business Card</title>
<link rel="stylesheet" href="https://fonts.googleapis.com/css2?family=Oswald:wght@500&family=Work+Sans:wght@400;500;800&display=swap">
<style>
  :root {
    --navy: #302a72;
    --red: #d8262d;
    --white: #ffffff;
    --ink: #4a4a55;
    --bg: #e6e6e8;
  }
  * { box-sizing: border-box; margin: 0; padding: 0; }
  html, body { width: 1200px; height: 900px; overflow: hidden; background: var(--bg); }
  body { position: relative; font-family: "Work Sans", sans-serif; }

  .card {
    position: absolute;
    left: 250px;
    width: 700px;
    height: 400px;
    overflow: hidden;
    box-shadow: 0 6px 18px rgba(0,0,0,.18);
  }
  .card--front { top: 36px; background: var(--white); }
  .card--back { top: 464px; background: var(--navy); }

  .front-waves { position: absolute; inset: 0; width: 700px; height: 400px; }

  .agent { position: absolute; top: 14px; right: 36px; text-align: right; color: var(--white); }
  .agent__name { font-family: "Oswald", sans-serif; font-weight: 500; font-size: 32px; letter-spacing: 1px; line-height: 1.1; }
  .agent__title { font-size: 13px; }

  .brokerage {
    position: absolute; display: flex; align-items: center; gap: 10px;
    font-weight: 800; color: var(--navy); letter-spacing: -.5px; white-space: nowrap;
  }
  .brokerage__mark { width: 16px; height: 16px; background: var(--red); flex: none; }
  .card--front .brokerage { left: 40px; top: 212px; font-size: 26px; }
  .card--back .brokerage { left: 0; right: 0; top: 168px; justify-content: center; font-size: 34px; color: var(--white); }
  .card--back .brokerage__mark { width: 20px; height: 20px; }

  .divider { position: absolute; left: 40px; right: 40px; top: 262px; height: 1px; background: var(--navy); }

  .contact { position: absolute; left: 40px; top: 282px; list-style: none; font-size: 16px; color: var(--ink); letter-spacing: .5px; }
  .contact li { display: flex; align-items: center; gap: 14px; height: 25px; }
  .contact svg { width: 14px; height: 14px; flex: none; }
  .contact .accent { color: var(--red); }

  .address { position: absolute; right: 40px; top: 286px; text-align: right; font-size: 16px; line-height: 1.5; color: var(--ink); letter-spacing: .5px; font-style: normal; }

  .badges { position: absolute; right: 40px; top: 346px; display: flex; gap: 12px; }
  .badge { width: 32px; height: 32px; border: 2px solid var(--navy); }
  .badge--round { border-radius: 50%; }

  .back-site { position: absolute; left: 0; right: 0; bottom: 46px; text-align: center; color: var(--white); font-size: 18px; letter-spacing: .8px; }
</style>
</head>
<body>

<section class="card card--front" aria-label="Card front">
  <svg class="front-waves" viewBox="0 0 700 400" aria-hidden="true">
    <path fill="var(--navy)" d="M0 0H700V60C560 108 380 126 220 130C120 134 44 144 0 156Z"/>
    <path fill="var(--red)" d="M0 168C44 156 120 144 220 140C390 134 560 114 700 68V78C560 126 390 148 225 154C125 158 48 170 0 184Z"/>
    <path fill="var(--navy)" d="M0 192C50 180 130 168 230 164C390 158 560 138 700 88V92C560 144 390 166 232 172C132 176 52 188 0 199Z"/>
  </svg>

  <div class="agent">
    <div class="agent__name">TOBIAS MERROW</div>
    <div class="agent__title">Realtor</div>
  </div>

  <div class="brokerage"><span class="brokerage__mark"></span>Brightpath Realty Group</div>

  <div class="divider"></div>

  <ul class="contact">
    <li>
      <svg viewBox="0 0 14 14" aria-hidden="true"><rect x="3" y="1" width="8" height="12" rx="1.5" fill="none" stroke="var(--navy)" stroke-width="1.5"/><circle cx="7" cy="10.5" r=".9" fill="var(--navy)"/></svg>
      407. 555. 0142
    </li>
    <li>
      <svg viewBox="0 0 14 14" aria-hidden="true"><path d="M3 1.5l2.5 2.5-1.5 1.8c.8 1.6 2 2.8 3.6 3.6l1.8-1.5 2.5 2.5-1.6 1.8C6 11.5 2.5 8 1.5 3.2Z" fill="var(--navy)"/></svg>
      407. 555. 0198
    </li>
    <li>
      <svg viewBox="0 0 14 14" aria-hidden="true"><rect x="1" y="3" width="12" height="8.5" fill="none" stroke="var(--navy)" stroke-width="1.4"/><path d="M1 3.5l6 4.5 6-4.5" fill="none" stroke="var(--navy)" stroke-width="1.4"/></svg>
      info@tobiasmerrowkl.com
    </li>
    <li>
      <svg viewBox="0 0 14 14" aria-hidden="true"><circle cx="7" cy="7" r="5.5" fill="none" stroke="var(--navy)" stroke-width="1.4"/><path d="M1.5 7h11M7 1.5c-2.5 3-2.5 8 0 11M7 1.5c2.5 3 2.5 8 0 11" fill="none" stroke="var(--navy)" stroke-width="1.1"/></svg>
      <span>www.<span class="accent">tobiasmerrowkl</span>.com</span>
    </li>
  </ul>

  <address class="address">
    480 Lakeview Court<br>
    Maitland Springs, FL 32700
  </address>

  <div class="badges">
    <span class="badge" role="img" aria-label="Realtor association badge"></span>
    <span class="badge badge--round" role="img" aria-label="Fair housing badge"></span>
  </div>
</section>

<section class="card card--back" aria-label="Card back">
  <div class="brokerage"><span class="brokerage__mark"></span>Brightpath Realty Group</div>
  <div class="back-site">www.tobiasmerrowkl.com</div>
</section>

</body>
</html>
```